Creating a website for a life changing company (Halvra Q)

We do need a website for our Coaching and Consulting business we recently launched. We do need it for information purposes and that our clients do have the opportunity to subscribe for packages, programs etc.
We would like to see designs which use the colours blue and yellow (see attachment). The final design should communicate our passion for the potential in people and the benefit (rising onward) for them.
Updates
Additional information:
Our company (webpage): Halvra Q (the C stands for "what people cannot see / imagine now...)
Welcome to Halvra Q(uarry)
Consulting (O.R.T.) & Coaching (Rise onward)
Two pillars:
1) O.R.T. ( Steward pathway - Our program - focussing on companies - business orientated)
2) Rise onward (Daily renewal - Events - focusing on individuals - primarily life changing)
For both of them we offer: Lanternhall & Halvra Q+ (This should go as a subscription)
Eventually you can draft this as a rhombus
Industry/Entity Type
Coaching / Consulting
Coding
Coded - Design and coding required
Number of Pages Required
1 page
Font styles to use
Other font styles liked:
- Lato
Requirements
Must have
- Please see attachment (About us / Offers / Calendar function / Links to Snapline and Linkwell account / mailing list / page for clients
Nice to have
- A banner

```html
<!DOCTYPE html>
<html lang="en">
<head>
<meta charset="utf-8">
<title>Halvra Q — Coaching &amp; Consulting</title>
<link href="https://fonts.googleapis.com/css2?family=Lato:wght@400;700;900&display=swap" rel="stylesheet">
<style>
:root{
  --blue:#0a6fb7;
  --yellow:#fff200;
  --ink:#333333;
  --text:#3a3a3a;
  --pale:#c9dcef;
  --footer:#2d2d2d;
  --white:#ffffff;
}
*{margin:0;padding:0;box-sizing:border-box}
html,body{width:1200px;height:4031px;overflow:hidden}
body{font-family:"Lato",Arial,sans-serif;color:var(--text);background:var(--white);position:relative}
.abs{position:absolute}
.site-header{position:absolute;top:0;left:0;width:1200px;height:105px;background:var(--white);border-bottom:1px solid #e6e6e6}
.brand{position:absolute;left:75px;top:28px;height:50px;display:flex;align-items:center;gap:16px}
.brand .dash{width:20px;height:2px;background:var(--blue)}
.brand .mark{width:26px;height:26px;border-radius:50%;background:var(--yellow)}
.brand .name{font-weight:700;font-size:15px;letter-spacing:3px;color:var(--blue)}
.main-nav{position:absolute;top:46px;right:75px;display:flex;gap:26px;font-size:13.5px;font-weight:700;color:#222;letter-spacing:.2px}
.hero{position:absolute;top:105px;left:0;width:1200px;height:700px}
.hero-photo{position:absolute;inset:0;background:linear-gradient(100deg,#6b7784 0%,#9ea8ae 30%,#c7c2bb 55%,#b46b5f 78%,#d9dde0 100%)}
.hero-shade{position:absolute;inset:0;background:linear-gradient(90deg,rgba(20,30,45,.45),rgba(20,30,45,0) 60%)}
.hero-copy{position:absolute;left:75px;top:142px;color:var(--white)}
.hero-copy .pre{font-size:57px;font-weight:900;line-height:1}
.hero-copy h1{font-size:96px;font-weight:900;line-height:1.05}
.hero-copy p{font-size:28px;line-height:39px;margin-top:14px;font-weight:400}
.btn{display:inline-flex;align-items:center;justify-content:center;background:var(--yellow);color:#222;font-weight:700;font-size:14.5px;border-radius:26px;height:51px;letter-spacing:.2px}
.hero .btn{position:absolute;left:75px;top:406px;width:263px}
.wave{position:absolute;left:0;width:1200px}
.section-title{position:absolute;left:0;width:1200px;text-align:center;font-size:52px;font-weight:700;color:var(--ink);letter-spacing:.5px}
.section-title span,.block-title span{color:var(--blue)}
.rule{position:absolute;height:4px;width:50px;background:var(--blue)}
.rule.center{left:575px}
.about-accent{left:75px;top:942px;width:90px;height:321px;background:var(--yellow);border-radius:12px}
.photo{border-radius:14px}
.about-photo{left:150px;top:887px;width:437px;height:432px;background:linear-gradient(120deg,#2b3d5c,#6c7f8f 45%,#2f8e98 65%,#4b5158)}
.block-title{position:absolute;font-size:52px;font-weight:700;color:var(--ink)}
.about-text{left:616px;top:1025px;width:500px;font-size:16px;line-height:31.3px;color:#333}
.about-btn{left:616px;top:1220px;width:394px}
.band{position:absolute;left:0;width:1200px;background:var(--pale)}
.lede{position:absolute;left:0;width:1200px;text-align:center;font-size:19px;color:#222}
.card-img{position:absolute;width:328px;height:222px;border-radius:12px}
.card-label{position:absolute;width:328px;text-align:center;font-size:23px;font-weight:700;color:var(--blue)}
.prog-title{position:absolute;width:328px;text-align:center;font-size:19px;font-weight:700;color:#222;line-height:28px}
.prog-title b{color:var(--blue)}
.prog-text{position:absolute;width:328px;text-align:center;font-size:16.5px;line-height:28px;color:#333}
.promo-accent{left:1040px;top:2899px;width:86px;height:321px;background:var(--yellow);border-radius:12px}
.promo-photo{left:613px;top:2844px;width:437px;height:432px;background:linear-gradient(100deg,#2f3a4e,#c9a335 30%,#3a4354 55%,#20355f 80%,#2b3344)}
.promo-sub{left:75px;top:3012px;font-size:29px;font-weight:700;color:#222}
.promo-text{left:75px;top:3054px;width:520px;font-size:24.5px;line-height:38px;color:#333}
.promo-btn{left:75px;top:3159px;width:182px}
.signup{position:absolute;left:285px;top:3673px;display:flex;gap:12px}
.signup .field{width:438px;height:54px;border:1px solid #aaa;border-radius:27px;display:flex;align-items:center;padding-left:24px;font-size:16.5px;color:#555;background:var(--white)}
.signup .btn{width:182px;height:54px;border-radius:27px}
.site-footer{position:absolute;left:0;top:3802px;width:1200px;height:229px;background:var(--footer);color:var(--white)}
.footer-nav{position:absolute;top:62px;left:0;width:1200px;display:flex;justify-content:center;gap:26px;font-size:14px;font-weight:700}
.copyright{position:absolute;top:100px;left:0;width:1200px;text-align:center;font-size:14.5px}
.social{position:absolute;top:143px;left:0;width:1200px;display:flex;justify-content:center;gap:22px;font-size:14px;font-weight:700}
.social span{display:flex;align-items:center;gap:6px}
.social i{display:block;width:12px;height:12px;border-radius:50%;background:var(--white)}
</style>
</head>
<body>

<header class="site-header">
  <div class="brand"><span class="dash"></span><span class="mark"></span><span class="name">HALVRA Q</span><span class="dash"></span></div>
  <nav class="main-nav">
    <span>HALVRA</span><span>ABOUT</span><span>O.R.T.</span><span>LANTERNHALL</span><span>RISE ONWARD</span><span>HALVRA Q+</span><span>TESTIMONIALS</span><span>CONTACT US</span>
  </nav>
</header>

<section class="hero">
  <div class="hero-photo" role="img" aria-label="Coach and client in a cheerful conversation at an office desk"></div>
  <div class="hero-shade"></div>
  <div class="hero-copy">
    <div class="pre">Welcome to</div>
    <h1>Halvra Q</h1>
    <p>Where Passion for igniting People's Potential<br>is in our DNA and brought Us together.</p>
  </div>
  <a class="btn">BOOK YOUR SESSION</a>
</section>

<svg class="wave" style="top:660px" width="1200" height="150" viewBox="0 0 1200 150">
  <path d="M0,60 C260,170 620,60 1050,32 C1120,27 1170,18 1200,0 L1200,150 L0,150 Z" fill="#ffffff"/>
  <path d="M0,48 C260,175 640,55 1050,32 C640,72 300,185 0,62 Z" fill="#0a6fb7"/>
</svg>

<div class="abs about-accent"></div>
<div class="abs photo about-photo" role="img" aria-label="The two founders standing outdoors, smiling"></div>
<h2 class="block-title" style="left:616px;top:920px">ABOUT <span>US</span></h2>
<div class="rule" style="left:616px;top:993px;width:94px"></div>
<p class="abs about-text">Welcome to Halvra Q, where Passion for igniting People's Potential is in our DNA and brought Us together. The journey starts in the Himalayas to Everest Base Camp, where transformation happened for both of them, it was rising onward (Q) what they could see, comprehend and imagine.</p>
<a class="abs btn about-btn">LEARN MORE ABOUT MARA AND TOBIAS</a>

<svg class="wave" style="top:1380px" width="1200" height="130" viewBox="0 0 1200 130">
  <path d="M0,100 C300,-5 700,85 1050,112 C1120,104 1170,70 1200,40 L1200,130 L0,130 Z" fill="#c9dcef"/>
  <path d="M0,100 C260,-5 620,15 1050,114 C640,55 300,25 0,102 Z" fill="#0a6fb7"/>
</svg>
<div class="band" style="top:1508px;height:597px"></div>

<h2 class="section-title" style="top:1570px">LANTERNHALL <span>PACKAGES</span></h2>
<div class="rule center" style="top:1644px"></div>
<p class="lede" style="top:1679px">Lanternhall Package offers you an ongoing partnership as you navigate your journey to reach your full potential.</p>

<div class="card-img" style="left:75px;top:1748px;background:linear-gradient(120deg,#3b3a36,#8d8880 50%,#d4d1cb)" role="img" aria-label="Coach presenting to a small group in a bright office"></div>
<div class="card-img" style="left:436px;top:1748px;background:linear-gradient(120deg,#cfd6dc,#5c78a8 45%,#2b3557 75%,#c9c4bd)" role="img" aria-label="Consultant and client reviewing a tablet together"></div>
<div class="card-img" style="left:798px;top:1748px;background:linear-gradient(120deg,#efece6,#b07a4c 40%,#3b2b25 75%,#dcd8d1)" role="img" aria-label="Two women talking across a table in a relaxed chat"></div>
<div class="card-label" style="left:75px;top:1990px">COACHING</div>
<div class="card-label" style="left:436px;top:1990px">CONSULTING</div>
<div class="card-label" style="left:798px;top:1990px">FIRESIDE CHAT</div>

<h2 class="section-title" style="top:2170px">RISE ONWARD <span>PROGRAM</span></h2>
<div class="rule center" style="top:2244px"></div>

<div class="card-img" style="left:75px;top:2287px;background:linear-gradient(160deg,#c6d0d6,#6f8a6a 45%,#4d6b3c 75%,#b99a6a)" role="img" aria-label="Hiker with a backpack facing a green mountain valley"></div>
<div class="card-img" style="left:436px;top:2287px;background:linear-gradient(160deg,#d9dee0,#9f9a8a 45%,#6b5a45 70%,#8a7558)" role="img" aria-label="Backpack resting on a stone wall before mountains"></div>
<div class="card-img" style="left:798px;top:2287px;background:linear-gradient(160deg,#cfd2d4,#7a6d62 50%,#5d4a36 80%,#b48a5d)" role="img" aria-label="Group of hikers climbing a rocky hillside at sunset"></div>

<div class="prog-title" style="left:75px;top:2538px"><b>RISE ONWARD LIGHT</b> (HALF DAY)</div>
<div class="prog-title" style="left:436px;top:2538px"><b>RISE ONWARD LIGHT</b>&nbsp; (2-3 DAYS)</div>
<div class="prog-title" style="left:798px;top:2538px"><b>RISE ONWARD UNLIMITED</b><br>(1 WEEK)</div>
<p class="prog-text" style="left:75px;top:2572px">This is a fantastic opportunity to understand, WHY you carry the heavy backpack throughout your life.</p>
<p class="prog-text" style="left:436px;top:2572px">We invite you to unpack your backpack, inspect the items you are carrying and decide WHAT to carry.</p>
<p class="prog-text" style="left:798px;top:2600px">You design your new backpack and decide HOW you want to carry it through your life.</p>

<div class="band" style="top:2744px;height:660px"></div>
<div class="abs promo-accent"></div>
<div class="abs photo promo-photo" role="img" aria-label="Two colleagues giving each other a high five"></div>
<h2 class="block-title" style="left:75px;top:2893px">HALVRA <span>Q</span></h2>
<div class="rule" style="left:75px;top:2966px;width:50px"></div>
<div class="abs promo-sub">We O.R.T. your Company</div>
<p class="abs promo-text">We ignite the Passion in People to unleash their full Potential!</p>
<a class="abs btn promo-btn">LEARN MORE</a>

<svg class="wave" style="top:3340px" width="1200" height="130" viewBox="0 0 1200 130">
  <path d="M0,70 C200,10 600,135 900,112 C1060,100 1150,60 1200,22 L1200,130 L0,130 Z" fill="#ffffff"/>
  <path d="M150,18 C450,15 640,135 900,112 C1060,98 1150,60 1200,22 C1150,70 1060,118 900,124 C620,140 430,35 150,18 Z" fill="#0a6fb7"/>
</svg>

<h2 class="section-title" style="top:3508px">JOIN <span>EMAIL LISTING</span></h2>
<div class="rule center" style="top:3582px"></div>
<p class="lede" style="top:3622px">Duis aute irure dolor in reprehenderit in voluptate velit esse cillum dolore eu fugiat nulla pariatu.</p>
<form class="signup">
  <div class="field">Enter Email Address</div>
  <a class="btn">SUBSCRIBE</a>
</form>

<footer class="site-footer">
  <nav class="footer-nav">
    <span>HOME</span><span>HALVRA</span><span>ABOUT</span><span>O.R.T.</span><span>LANTERNHALL</span><span>RISE ONWARD</span><span>HALVRA Q+</span><span>TESTIMONIALS</span><span>CONTACT US</span>
  </nav>
  <p class="copyright">Copyright © 2022&nbsp; CompanyName All Right Reserved</p>
  <div class="social">
    <span><i></i>Chatter</span><span><i></i>Snapline</span><span><i></i>Linkwell</span>
  </div>
</footer>

</body>
</html>
```